Coffeeshop menu for filter tip

We want to have a cannabis (coffeeshop) menu in the size 25mm wide x 60mm wide. Some examples attached.

it must have the following text:
Menu

WEED p/g
Oblivane €16
Cloudplum €14
Tide Runner €14
Quincefig €16
Mega Marsh €14
Grey Heron €14

HASH p/g
Tashar Amber €12
Pebble Frost€11
Lime Dunes €14
Ash Petal €10

Target Market(s)

tourist in Amsterdam

Requirements
Nice to have
• cannabis sign leaf
• No Cigarettes allowed symbol

```html
<!DOCTYPE html>
<html lang="en">
<head>
<meta charset="utf-8">
<title>Coffeeshop Menu</title>
<link rel="stylesheet" href="https://fonts.googleapis.com/css2?family=Questrial&display=swap">
<style>
  :root {
    --bg: #0c0d0c;
    --bg-leaf: #1d211d;
    --panel-weed: #1c1c1c;
    --panel-hash: #0a0a0a;
    --band: #000000;
    --skyline: #050505;
    --accent: #f4f03a;
    --light: #ffffff;
    --muted: #9a9a9a;
  }
  html, body {
    margin: 0;
    padding: 0;
    width: 1200px;
    height: 2880px;
    overflow: hidden;
    background: var(--bg);
  }
  .menu-card {
    display: block;
    width: 1200px;
    height: 2880px;
    font-family: "Questrial", sans-serif;
  }
  .notice { fill: var(--light); font-size: 26px; letter-spacing: 5px; }
  .notice-icon { fill: none; stroke: var(--light); stroke-width: 2.4; }
  .section-title { fill: var(--accent); font-size: 80px; }
  .unit { fill: var(--muted); font-size: 40px; }
  .item-name { fill: var(--accent); font-size: 42px; letter-spacing: 9px; }
  .item-price { fill: var(--light); font-size: 47px; letter-spacing: -1.5px; }
  .panel-weed { fill: var(--panel-weed); }
  .panel-hash { fill: var(--panel-hash); }
  .footer-band { fill: var(--band); }
  .footer-title { fill: var(--light); font-size: 92px; }
</style>
</head>
<body>
<svg class="menu-card" viewBox="0 0 750 1800" xmlns="http://www.w3.org/2000/svg">
  <defs>
    <radialGradient id="leafGlow" cx="0.55" cy="0.45" r="0.7">
      <stop offset="0" stop-color="var(--bg-leaf)"/>
      <stop offset="1" stop-color="var(--bg)"/>
    </radialGradient>
  </defs>

  <rect class="backdrop" x="0" y="0" width="750" height="1800" fill="url(#leafGlow)"
        role="img" aria-label="Faint cannabis leaf illustrations across the dark background"/>

  <g class="notice-line">
    <text class="notice" x="218" y="62">NO CIGARETTES</text>
    <g class="notice-icon">
      <circle cx="516" cy="53" r="12"/>
      <rect x="507" y="51" width="15" height="5"/>
      <line x1="507.5" y1="44.5" x2="524.5" y2="61.5"/>
    </g>
  </g>

  <g class="section weed">
    <polygon class="panel-weed" points="540,157 688,157 688,910 63,910 63,232 515,232"/>
    <text class="section-title" x="98 245 350 458" y="211">WEED</text>
    <text class="unit" x="588" y="238">p/g</text>

    <text class="item-name" x="108" y="338">OBLIVANE</text>
    <text class="item-price" x="653" y="338" text-anchor="end">€16</text>
    <text class="item-name" x="108" y="441">CLOUDPLUM</text>
    <text class="item-price" x="653" y="441" text-anchor="end">€14</text>
    <text class="item-name" x="108" y="544">TIDE RUNNER</text>
    <text class="item-price" x="653" y="544" text-anchor="end">€14</text>
    <text class="item-name" x="108" y="647">QUINCEFIG</text>
    <text class="item-price" x="653" y="647" text-anchor="end">€16</text>
    <text class="item-name" x="108" y="750">MEGA MARSH</text>
    <text class="item-price" x="653" y="750" text-anchor="end">€14</text>
    <text class="item-name" x="108" y="853">GREY HERON</text>
    <text class="item-price" x="653" y="853" text-anchor="end">€14</text>
  </g>

  <g class="section hash">
    <polygon class="panel-hash" points="63,1007 155,1007 230,1082 688,1082 688,1548 63,1548"/>
    <text class="section-title" x="258 375 492 600" y="1063">HASH</text>
    <text class="unit" x="105" y="1083">p/g</text>

    <text class="item-price" x="170" y="1185" text-anchor="end">€12</text>
    <text class="item-name" x="215" y="1185">TASHAR AMBER</text>
    <text class="item-price" x="170" y="1288" text-anchor="end">€11</text>
    <text class="item-name" x="215" y="1288">PEBBLE FROST</text>
    <text class="item-price" x="170" y="1390" text-anchor="end">€14</text>
    <text class="item-name" x="215" y="1390">LIME DUNES</text>
    <text class="item-price" x="170" y="1493" text-anchor="end">€10</text>
    <text class="item-name" x="215" y="1493">ASH PETAL</text>
  </g>

  <rect class="skyline" x="0" y="1570" width="750" height="92" fill="var(--skyline)"
        role="img" aria-label="Silhouette of the Amsterdam skyline"/>

  <g class="footer">
    <rect class="footer-band" x="0" y="1660" width="750" height="140"/>
    <text class="footer-title" x="155 295 410 545" y="1758">MENU</text>
  </g>
</svg>
</body>
</html>
```